Document Processing Services and Solutions for School Systems

I am looking to design a brochure for both Digital and Paper use. I can supply the written content. Would be looking for an overall design of the brochure with provided content worked into it.

```html
<!DOCTYPE html>
<html lang="en">
<head>
<meta charset="utf-8">
<title>Nexora Systems – School Document Management Brochure</title>
<link href="https://fonts.googleapis.com/css2?family=Montserrat:ital,wght@0,400;0,500;0,600;0,700;0,800;1,600;1,800;1,900&display=swap" rel="stylesheet">
<style>
  :root{
    --navy:#2e2f8f;
    --navy-deep:#24257a;
    --gold:#c89e0f;
    --gold-light:#d9b23a;
    --ink:#1d1d3a;
    --paper:#ffffff;
    --canvas:#ffffff;
  }
  *{box-sizing:border-box;margin:0;padding:0}
  html,body{width:1200px;height:5324px;overflow:hidden;background:var(--canvas)}
  body{position:relative;font-family:"Montserrat",sans-serif;color:var(--ink)}
  .usage-label{position:absolute;top:222px;left:0;width:1200px;text-align:center;font-size:30px;font-weight:500;letter-spacing:1px;color:#111}
  .page{position:absolute;left:234px;width:734px;height:1134px;background:var(--paper);overflow:hidden;box-shadow:0 18px 40px rgba(0,0,0,.28)}
  .page--cover{top:321px}
  .page--services{top:1535px}
  .page--why{top:2752px}
  .page--contact{top:3964px}
  .abs{position:absolute}
  .headline{font-weight:900;font-style:italic;line-height:.92;text-transform:uppercase}
  .brand{position:absolute;display:flex;align-items:center;gap:10px;font-weight:800;color:var(--navy);white-space:nowrap}
  .brand__dot{width:14px;height:14px;background:var(--gold)}
  .photo{position:absolute}
  .footer-stripe{position:absolute;left:0;bottom:0;width:100%;height:7px;background:var(--navy)}
  .gold-rule{position:absolute;left:0;width:100%;height:6px;background:var(--gold)}
  .site-url{position:absolute;font-weight:700;font-size:22px;color:var(--ink)}

  /* cover */
  .cover__kicker{left:46px;top:295px;width:372px;height:38px;background:var(--gold);color:var(--navy);font-size:30px;line-height:38px;padding-left:14px}
  .cover__title{left:46px;top:352px;font-size:52px;color:var(--navy)}
  .cover__band{left:0;top:550px;width:100%;height:135px;background:var(--gold)}
  .cover__tag{left:46px;top:534px;width:172px;height:38px;background:var(--navy);color:#fff;font-size:25px;line-height:38px;padding-left:12px}
  .cover__sub{left:46px;top:586px;font-size:38px;color:#fff}
  .cover__panel{left:0;top:685px;width:520px;height:279px;background:var(--navy)}
  .cover__pillars{left:50px;top:708px;font-size:30px;line-height:1.17;color:var(--gold-light)}
  .cover__pillars span{display:block}
  .cover__intro{left:46px;top:832px;width:300px;font-size:12.5px;line-height:1.3;color:#fff}

  /* services */
  .section-title{left:77px;font-size:52px}
  .section-title .navy{color:var(--navy)}
  .section-title .gold{color:var(--gold)}
  .service{position:absolute;left:0;width:734px;height:259px;border-top:2px solid var(--gold);border-bottom:2px solid var(--gold)}
  .service__icon{position:absolute;left:67px;top:22px;width:62px;height:62px;border-radius:50%;background:var(--navy);border:3px solid #fff;box-shadow:0 0 0 3px var(--navy)}
  .service__icon svg{width:100%;height:100%}
  .service__title{position:absolute;left:155px;top:20px;font-size:27px;color:var(--navy);line-height:.85}
  .service__list{position:absolute;left:72px;list-style:none;width:330px}
  .service__list li{position:relative;padding-left:24px;font-size:13px;line-height:1.3;margin-bottom:14px;font-weight:500}
  .service__list li::before{content:"";position:absolute;left:0;top:4px;width:9px;height:9px;border:2px solid var(--gold);border-radius:50%}
  .service__photo{position:absolute;left:418px;width:262px;height:262px;border-radius:50%;border:3px solid var(--gold)}

  /* why */
  .why__panel{left:97px;top:248px;width:637px;height:700px;background:var(--navy);border-radius:44px 0 0 44px}
  .benefit{position:absolute;left:57px;width:400px;height:120px}
  .benefit__icon{position:absolute;left:0;top:0;width:92px;height:92px;border-radius:50%;background:var(--gold);border:4px solid #fff;box-shadow:0 0 0 3px var(--navy)}
  .benefit__icon svg{width:100%;height:100%}
  .benefit__title{position:absolute;left:117px;top:0;font-size:27px;font-weight:600;font-style:italic;color:var(--gold-light);white-space:nowrap}
  .benefit__text{position:absolute;left:117px;top:40px;width:270px;font-size:16px;line-height:1.35;color:#fff}
  .benefit__rule{position:absolute;left:117px;top:118px;width:270px;height:1px;background:rgba(255,255,255,.25)}

  /* contact */
  .contact__title{left:70px;top:281px;font-size:38px;color:var(--navy)}
  .contact__title .gold{color:var(--gold)}
  .contact__band{left:0;top:523px;width:100%;height:157px;background:var(--gold)}
  .contact__panel{left:0;top:680px;width:100%;height:288px;background:var(--navy)}
  .contact__lead{left:71px;top:714px;font-size:20px;font-weight:500;line-height:1.25;color:#fff;text-transform:uppercase}
  .contact__cta{left:71px;top:792px;font-size:39px;color:var(--gold-light);line-height:1}
  .contact__note{left:71px;top:884px;width:440px;font-size:14px;line-height:1.4;color:#fff;font-weight:500}
  .contact__list{position:absolute;left:74px;top:1004px;list-style:none}
  .contact__list li{display:flex;align-items:center;gap:12px;font-size:15px;font-weight:600;height:27px}
  .contact__list svg{width:15px;height:15px}
</style>
</head>
<body>

<div class="usage-label">FOR DIGITAL USE</div>

<!-- Cover -->
<section class="page page--cover">
  <div class="abs cover__band"></div>
  <div class="abs cover__panel"></div>
  <div class="photo" role="img" aria-label="Smiling office worker with glasses holding a tall stack of binders and folders" style="left:356px;top:384px;width:378px;height:750px;background:linear-gradient(180deg,#ece8e3 0%,#e2dbd2 30%,#d9d0c6 60%,#c9c4be 100%);clip-path:polygon(46% 0,100% 0,100% 100%,0 100%,0 42%,24% 40%,30% 30%,40% 26%)"></div>
  <div class="brand" style="left:66px;top:110px;font-size:52px"><span class="brand__dot"></span>Nexora Systems</div>
  <div class="abs headline cover__kicker">Transform your</div>
  <h1 class="abs headline cover__title">School’s<br>Document<br>Management</h1>
  <div class="abs headline cover__tag">With our</div>
  <div class="abs headline cover__sub">Comprehensive<br>Solutions</div>
  <div class="abs headline cover__pillars"><span>Streamline</span><span>Secure</span><span>Simplify</span></div>
  <p class="abs cover__intro">Managing school documents efficiently is crucial for smooth operations, compliance, and productivity. Our document processing services provide innovative solutions tailored for educational institutions, ensuring secure and seamless document and data handling.</p>
  <div class="gold-rule" style="top:964px;width:356px"></div>
  <div class="site-url" style="left:46px;top:1040px">www.nexorasys.com</div>
  <div class="footer-stripe"></div>
</section>

<!-- Services -->
<section class="page page--services">
  <h2 class="abs headline section-title" style="top:62px"><span class="navy">Our</span><br><span class="gold">Services</span></h2>
  <div class="brand" style="left:498px;top:84px;font-size:26px"><span class="brand__dot" style="width:9px;height:9px"></span>Nexora</div>

  <div class="service" style="top:186px">
    <div class="service__icon"><svg viewBox="0 0 62 62"><rect x="20" y="16" width="22" height="30" rx="2" fill="none" stroke="#fff" stroke-width="3"/><line x1="14" y1="31" x2="48" y2="31" stroke="#fff" stroke-width="3"/></svg></div>
    <h3 class="service__title headline">Document<br>Scanning<br>&amp; Conversion</h3>
    <ul class="service__list" style="top:104px">
      <li>Convert paper records into digital formats for easy access and storage.</li>
      <li>High-speed scanning for student records, administrative files, and historical archives.</li>
      <li>OCR (Optical Character Recognition) for searchable and editable documents.</li>
    </ul>
    <div class="service__photo" role="img" aria-label="Staff member scanning paper files at an office scanner" style="top:-2px;background:linear-gradient(135deg,#e6e8ee,#aab1c0 60%,#5e6677)"></div>
  </div>

  <div class="service" style="top:492px">
    <div class="service__icon"><svg viewBox="0 0 62 62"><path d="M20 40h22a8 8 0 0 0 0-16 11 11 0 0 0-21-2 9 9 0 0 0-1 18z" fill="none" stroke="#fff" stroke-width="3"/></svg></div>
    <h3 class="service__title headline">Cloud-Based<br>Document<br>Management</h3>
    <ul class="service__list" style="top:104px">
      <li>Secure, centralized document storage accessible from anywhere.</li>
      <li>Role-based access controls for administrators, teachers, and staff.</li>
      <li>Automated backups and compliance with educational data security standards.</li>
    </ul>
    <div class="service__photo" role="img" aria-label="Hand touching a glowing cloud storage network graphic" style="top:-2px;background:radial-gradient(circle at 55% 50%,#8fb4e8,#22355c 55%,#0b1428)"></div>
  </div>

  <div class="service" style="top:797px">
    <div class="service__icon"><svg viewBox="0 0 62 62"><circle cx="31" cy="31" r="8" fill="none" stroke="#fff" stroke-width="3"/><circle cx="31" cy="31" r="15" fill="none" stroke="#fff" stroke-width="3" stroke-dasharray="5 4"/></svg></div>
    <h3 class="service__title headline">Workflow<br>Automation</h3>
    <ul class="service__list" style="top:96px">
      <li>Digitize and streamline approval processes for enrollment, transcripts, and HR forms.</li>
      <li>Reduce paperwork and improve efficiency with automated workflows.</li>
      <li>Integration capable with existing school management systems.</li>
    </ul>
    <div class="service__photo" role="img" aria-label="Bright modern open-plan office with desks and large windows" style="top:-2px;background:linear-gradient(160deg,#f2f0ec,#c9c2b8 50%,#7d7468)"></div>
  </div>
</section>

<!-- Why choose us -->
<section class="page page--why">
  <h2 class="abs headline section-title" style="left:97px;top:62px"><span class="navy">Why</span><br><span class="gold">Choose<br>Us?</span></h2>
  <div class="brand" style="left:508px;top:84px;font-size:26px"><span class="brand__dot" style="width:9px;height:9px"></span>Nexora</div>
  <div class="abs why__panel"></div>
  <div class="photo" role="img" aria-label="Woman with glasses holding a stack of colourful binders" style="left:462px;top:383px;width:272px;height:751px;background:linear-gradient(180deg,#f1e6cc 0%,#efe3c8 20%,#f4f4f4 55%,#5fc6d6 75%,#e56e5c 90%,#222 100%);border-radius:120px 0 0 0"></div>

  <div class="benefit" style="top:306px">
    <div class="benefit__icon"><svg viewBox="0 0 92 92"><path d="M28 62V50M40 62V42M52 62V36M64 62V28" stroke="#fff" stroke-width="5" stroke-linecap="round"/></svg></div>
    <div class="benefit__title">Increased Efficiency</div>
    <p class="benefit__text">Save time with digital workflows and instant document retrieval.</p>
    <div class="benefit__rule"></div>
  </div>
  <div class="benefit" style="top:465px">
    <div class="benefit__icon"><svg viewBox="0 0 92 92"><path d="M46 24l18 7v14c0 11-8 20-18 23-10-3-18-12-18-23V31z" fill="none" stroke="#fff" stroke-width="4"/><path d="M38 46l6 6 10-11" fill="none" stroke="#fff" stroke-width="4"/></svg></div>
    <div class="benefit__title">Enhanced Security</div>
    <p class="benefit__text">Protect sensitive student &amp;faculty information.</p>
    <div class="benefit__rule"></div>
  </div>
  <div class="benefit" style="top:616px">
    <div class="benefit__icon"><svg viewBox="0 0 92 92"><circle cx="46" cy="40" r="13" fill="none" stroke="#fff" stroke-width="4"/><path d="M24 64h30l14-8" fill="none" stroke="#fff" stroke-width="4" stroke-linecap="round"/></svg></div>
    <div class="benefit__title">Cost Savings</div>
    <p class="benefit__text">Reduce paper, printing, and storage costs.</p>
    <div class="benefit__rule"></div>
  </div>
  <div class="benefit" style="top:775px">
    <div class="benefit__icon"><svg viewBox="0 0 92 92"><circle cx="46" cy="46" r="17" fill="none" stroke="#fff" stroke-width="4"/><path d="M46 29v34M29 46h34" stroke="#fff" stroke-width="3"/></svg></div>
    <div class="benefit__title">Eco-Friendly</div>
    <p class="benefit__text">Minimize your school’s carbon footprint by going digital.</p>
  </div>

  <div class="site-url" style="left:97px;top:1010px">www.nexorasys.com</div>
</section>

<!-- Contact -->
<section class="page page--contact">
  <div class="abs contact__band"></div>
  <div class="photo" role="img" aria-label="Two colleagues reviewing documents at a desk with a computer, archive shelves behind them" style="left:240px;top:120px;width:494px;height:560px;background:linear-gradient(180deg,#f2f2f5 0%,#e4e4ea 30%,#c9c3c0 70%,#b9b2ae 100%)"></div>
  <h2 class="abs headline contact__title">Get<br>Started<br><span class="gold">Today!</span></h2>
  <div class="abs contact__panel"></div>
  <p class="abs contact__lead">Let us help you modernize your<br>document processing system.</p>
  <p class="abs headline contact__cta">Contact us for a<br>free consultation</p>
  <p class="abs contact__note">and discover how our solutions can transform your school’s document management.</p>
  <div class="gold-rule" style="top:968px"></div>
  <ul class="contact__list">
    <li><svg viewBox="0 0 16 16"><circle cx="8" cy="8" r="8" fill="var(--gold)"/></svg>555-014-2290</li>
    <li><svg viewBox="0 0 16 16"><circle cx="8" cy="8" r="8" fill="var(--gold)"/></svg>info@nexorasys.com</li>
    <li><svg viewBox="0 0 16 16"><circle cx="8" cy="8" r="8" fill="var(--gold)"/></svg>www.nexorasys.com</li>
  </ul>
  <div class="brand" style="left:455px;top:1012px;font-size:36px"><span class="brand__dot" style="width:11px;height:11px"></span>Nexora</div>
  <div class="footer-stripe"></div>
</section>

</body>
</html>
```